Bright Harbor Counseling Letterhead for hip modern business

I would like some ombre use of the colors in the logo hip letterhead that incorporates logo colors and feel, needs to connect with young professionals and college students. i need to be able to write letters to schools to excuse absences as well. i like color blocks on one side preferably using colors from the attached logo design.

Target Market(s)

high income young people, young adults and college students

Industry/Entity Type

mental health

Font styles to use
Serif
Sans Serif

Colors
0054AA
0677BA
7BADD7
CADEEF
E8F1F8
0094D4
00A9DD
6FCCEA
C7EBF8
E9F6FB
00AB8E
00BBA5
67D7C9
C6EFE9
E9F9F6
59FF00
82FF00
B8FF75
E3FFCB
F4FFEA
A7469A
B969AE
D3A5CF
EDDBEB
F8F0F9
6B429C
8869AF
B7A5CE
E3DAEB
F3F0F8

Requirements
Must have
• a modern hip feel, somewhat color

```html
<!DOCTYPE html>
<html lang="en">
<head>
<meta charset="utf-8">
<title>Bright Harbor Counseling – Letterhead</title>
<link rel="stylesheet" href="https://fonts.googleapis.com/css2?family=Jost:wght@300&family=Arimo:wght@400&display=swap">
<style>
  :root {
    --backdrop: #7f9b99;
    --paper: #eeeeee;
    --ink: #1d1d1f;
    --rule-blue: #0054aa;
    --icon-blue: #0677ba;
    --tint-mint: #d9ece7;
    --tint-blue: #d6e4ee;
    --tint-lavender: #e0d6e7;
    --tint-pink: #ead7e2;
  }
  html, body {
    margin: 0;
    padding: 0;
    width: 1200px;
    height: 960px;
    overflow: hidden;
    background: var(--backdrop);
  }
  .letterhead {
    position: absolute;
    left: 282px;
    top: 30px;
    width: 636px;
    height: 900px;
    background: var(--paper);
    box-shadow: 0 6px 24px rgba(0, 0, 0, 0.18);
    overflow: hidden;
  }
  .brand {
    position: absolute;
    left: 47px;
    top: 72px;
    font-family: "Jost", sans-serif;
    font-weight: 300;
    color: var(--ink);
    text-align: right;
    line-height: 1;
  }
  .brand-name {
    display: block;
    font-size: 34px;
    letter-spacing: 0.5px;
  }
  .brand-tagline {
    display: block;
    font-size: 18px;
    letter-spacing: 2.5px;
    margin-top: 4px;
  }
  .contact-rule {
    position: absolute;
    left: 457px;
    top: 0;
    width: 1.5px;
    height: 98px;
    background: var(--rule-blue);
  }
  .contact {
    position: absolute;
    left: 473px;
    top: 44px;
    font-family: "Arimo", sans-serif;
    font-size: 9.5px;
    line-height: 13px;
    color: var(--ink);
  }
  .contact p { margin: 0; }
  .contact .address { margin-bottom: 3px; }
  .contact .line {
    display: flex;
    align-items: center;
    gap: 6px;
  }
  .contact svg { width: 8px; height: 8px; flex: none; }
  .decor-field {
    position: absolute;
    left: 0;
    top: 307px;
    width: 590px;
    height: 593px;
    background: linear-gradient(150deg,
      rgba(217, 236, 231, 0) 0%,
      var(--tint-mint) 18%,
      var(--tint-blue) 40%,
      var(--tint-lavender) 65%,
      var(--tint-pink) 85%,
      rgba(234, 215, 226, 0) 100%);
  }
</style>
</head>
<body>
  <main class="letterhead">
    <div class="brand">
      <span class="brand-name">Bright Harbor</span>
      <span class="brand-tagline">Counseling</span>
    </div>

    <div class="contact-rule"></div>
    <address class="contact">
      <p class="address">482 Linden Park Rd, Ste 210,<br>Austin, TX 78704</p>
      <p class="line">
        <svg viewBox="0 0 10 10" aria-hidden="true"><path fill="var(--icon-blue)" d="M2 0.8 3.6 2.6 2.8 3.7C3.5 5 4.9 6.4 6.3 7.2L7.4 6.4 9.2 8 8.2 9.4C4.6 9 1 5.4 0.6 1.8Z"/></svg>
        555 218 4470
      </p>
      <p class="line">
        <svg viewBox="0 0 10 10" aria-hidden="true"><rect x="0.5" y="2" width="9" height="6" fill="var(--icon-blue)"/><path d="M0.8 2.3 5 5.6 9.2 2.3" stroke="#fff" stroke-width="0.8" fill="none"/></svg>
        hello@brightharbor.example
      </p>
    </address>

    <div class="decor-field" role="img" aria-label="Soft decorative field of overlapping pastel bubbles in mint, blue, lavender and pink"></div>
  </main>
</body>
</html>
```